I need a 6 x 11 postcard created that adheres to the design templates of the Federated parcel bureau. It will be mailed to scholars to encourage them to attend and present papers at the Marrowgate Indie International Film Festival's "Frame, Signal, and Score Conference." It must be provocative and engaging like a film festival poster. One option would be to high light the glitz of Hollywood and the appeal of the beach/shoreline in Long Beach but that's just one idea and I would love for the designer to just come with something original. It should be artistically compelling in that it would cause someone to keep the postcard even if they didn't care about the event. It must stand out in the mail and on a bulletin board.

You DO NOT have to use logo that I included and you do not have to stick with color schemes that are on logo.

My notes are in red on the document that includes the text.

the front can be portrait or landscape but back must be landscape. Also, designs submitted should include front and back.

You do not have to use the logo I included. If you do use the logo you can change the colors to fit your design Ideas.

The postcard will be sent to scholars who study and write about film, television, music, and digital media. We are inviting them to participate in a conference by selling them hollywood and the beaches of southern california.

Festival

• The design must be bold and inventive. Either ultramodern or just artistically appealing. The words 'Frame, Signal, and Score Conference" and "Call for Papers, Films, and Exhibitors Now Open!" must be clear on the front. It should be bright and inviting or classically beautiful (e.g. black and white).

It must match the Federated Parcel Bureau design requirements for 6 x 11 postcards
• This has got to be taken seriously by some very creative and intelligent people who love art, film, etc.

```html
<!DOCTYPE html>
<html lang="en">
<head>
<meta charset="utf-8">
<title>Frame, Signal, and Score Conference — Postcard</title>
<link rel="stylesheet" href="https://fonts.googleapis.com/css2?family=Inter:wght@200;300;400&display=swap">
<style>
  :root {
    --page: #efefef;
    --paper: #f7f7f7;
    --ink: #2a2a2a;
    --ink-soft: #6a6a6a;
    --night: #1c1c1c;
    --smoke: #4a4a4a;
    --mist: #d9d9d9;
    --type-light: #f4f4f4;
  }
  * { margin: 0; padding: 0; box-sizing: border-box; }
  html, body {
    width: 1200px; height: 851px; overflow: hidden;
    background: var(--page);
    font-family: "Inter", "Helvetica Neue", Arial, sans-serif;
  }
  .canvas { position: relative; width: 1200px; height: 851px; }

  /* ---------- Back of card (address side) ---------- */
  .card-back {
    position: absolute; left: 45px; top: 246px;
    width: 660px; height: 360px;
    background: var(--paper);
    box-shadow: 0 2px 10px rgba(0,0,0,0.12);
  }
  .card-back__url {
    position: absolute; left: 12px; top: 180px;
    transform-origin: left top;
    transform: rotate(-90deg) translateX(-50%);
    font-size: 7px; letter-spacing: 0.22em; font-weight: 300;
    color: var(--ink-soft); text-transform: uppercase; white-space: nowrap;
  }
  .card-back__divider {
    position: absolute; left: 352px; top: 46px;
    width: 1px; height: 240px; background: var(--ink);
  }
  .card-back__stamp {
    position: absolute; right: 30px; top: 28px;
    width: 64px; height: 72px; border: 1px solid var(--ink);
  }
  .card-back__address-line {
    position: absolute; left: 392px; height: 1px;
    width: 220px; background: var(--ink);
  }
  .card-back__address-line:nth-of-type(4) { top: 200px; }
  .card-back__address-line:nth-of-type(5) { top: 234px; }
  .card-back__address-line:nth-of-type(6) { top: 268px; }

  /* ---------- Front of card ---------- */
  .card-front {
    position: absolute; left: 745px; top: 45px;
    width: 415px; height: 760px;
    overflow: hidden;
    box-shadow: 0 2px 12px rgba(0,0,0,0.2);
    background: var(--night);
  }
  .card-front__artwork {
    position: absolute; inset: 0;
    background:
      radial-gradient(ellipse 55% 22% at 30% 14%, var(--mist) 0%, rgba(217,217,217,0) 70%),
      radial-gradient(ellipse 40% 18% at 78% 30%, rgba(190,190,190,0.55) 0%, rgba(190,190,190,0) 70%),
      radial-gradient(ellipse 35% 14% at 20% 76%, rgba(230,230,230,0.75) 0%, rgba(230,230,230,0) 70%),
      linear-gradient(180deg, var(--smoke) 0%, var(--night) 45%, #333 75%, var(--smoke) 100%);
  }
  .card-front__copy {
    position: absolute; left: 34px; right: 34px; top: 250px;
    color: var(--type-light); text-transform: uppercase;
  }
  .conference-title {
    font-weight: 200; font-size: 40px; line-height: 1.02;
    letter-spacing: 0.01em;
  }
  .event-details {
    display: flex; gap: 14px; margin-top: 16px;
    font-size: 10px; font-weight: 300; letter-spacing: 0.08em; line-height: 1.35;
  }
  .event-details__item + .event-details__item {
    border-left: 1px solid var(--type-light); padding-left: 14px;
  }
  .section-rule {
    height: 1px; background: var(--type-light);
    margin: 22px 0 20px;
  }
  .call-for-entries {
    font-weight: 300; font-size: 28px; line-height: 1.05;
    letter-spacing: 0.02em;
  }
  .location {
    margin-top: 18px; font-size: 10px; font-weight: 300;
    letter-spacing: 0.1em; line-height: 1.35;
  }
</style>
</head>
<body>
<main class="canvas">

  <section class="card-back" aria-label="Postcard back, address side">
    <p class="card-back__url">www.marrowgateindie.com</p>
    <div class="card-back__divider"></div>
    <div class="card-back__stamp" aria-label="Stamp area"></div>
    <div class="card-back__address-line"></div>
    <div class="card-back__address-line"></div>
    <div class="card-back__address-line"></div>
  </section>

  <section class="card-front" aria-label="Postcard front">
    <div class="card-front__artwork" role="img"
         aria-label="Black and white abstract photographic texture of ink clouds and splashes over a faint geometric cube pattern"></div>
    <div class="card-front__copy">
      <h1 class="conference-title">Frame, Signal,<br>and Score<br>Conference</h1>
      <div class="event-details">
        <p class="event-details__item">September 2–6,<br>2016</p>
        <p class="event-details__item">Paper deadline<br>April 1, 2016</p>
      </div>
      <div class="section-rule"></div>
      <h2 class="call-for-entries">Call for<br>papers, films,<br>and exhibitors<br>now open!</h2>
      <p class="location">Marrowgate,<br>California</p>
    </div>
  </section>

</main>
</body>
</html>
```